Website design for luxury private hair salon

I'm looking for someone to use my Logo and build me a website for my webpage www.corsetresses.com.au (You can have a look at it as it has every detail I need included on it already), however I want a fresh new appearance and it to look and feel super stylish.

I am thinking colours in black, with silver or white, beautiful hair images like the ones you'll see on the current webpage - the price list as per what you already see.

I will include a copy of my biz card on here, so you can see the feel of the card, and design a website with a similar feel. It is matt black with a foil silver.

Modern, but classic and fresh. I will also need you to be able to publish it to my URL for me as I have no idea how to do this. I need it up and running pronto!

The website will need to be able to be read clearly on all devices incluing smart phones and ipads. The URL is currently registered and hosted by Norvel Web

Thinking a Home Page - large logo etc and write up on who and what we offer
Services/Price List page - as per the price list on my current webpage
Contact Page - with a built in contact form.

Target Market(s)

Middle aged, fashionable, stylish women and men who enjoy luxury hair care and styling in an upmarket location.

Industry/Entity Type

Hair And Beauty

Number of Pages Required

3 page

Font styles to use
Other font styles liked:
• see my images for my current logo

Colors
000000
b2b2b2
a54499

Requirements
Must have
• Style
• Fast turnaround
• Be viewable on all devices, PC, ipads, smart phones
• Designer able to upload it so its a running website for me to my URL
Nice to have
• Just a really feminine, stylish website which is easy to read and shows some beautiful images of perfect hair
Should not have
• Browns, reds or orange colours.

```html
<!DOCTYPE html>
<html lang="en">
<head>
<meta charset="utf-8">
<title>Velora Hair – Luxury Hair Salon</title>
<link rel="stylesheet" href="https://fonts.googleapis.com/css2?family=Open+Sans:ital,wght@0,400;0,600;1,400&family=Great+Vibes&family=Jost:wght@400&display=swap">
<style>
:root{
  --plum:#a54499;
  --plum-deep:#9a3a90;
  --ink:#222222;
  --grey:#777777;
  --silver:#b2b2b2;
  --paper:#ffffff;
  --mist:#f1f1f1;
  --night:#0d0d0d;
  --coal:#111111;
}
*{margin:0;padding:0;box-sizing:border-box}
html,body{width:1200px;height:2875px;overflow:hidden}
body{position:relative;background:var(--paper);font-family:"Open Sans",Arial,sans-serif;color:var(--ink)}
.abs{position:absolute}
.script{font-family:"Great Vibes",cursive;font-weight:400}

/* Hero */
.hero{left:0;top:0;width:1200px;height:638px;overflow:hidden}
.hero-photo{position:absolute;inset:0;background:
  radial-gradient(ellipse 380px 420px at 930px 250px,#8a7a72 0%,rgba(80,70,66,.6) 55%,transparent 80%),
  radial-gradient(ellipse 260px 300px at 470px 470px,#5b4a40 0%,transparent 75%),
  linear-gradient(100deg,#3a3735 0%,#4b4744 45%,#3b3634 100%)}
.hero-shade{position:absolute;inset:0;background:rgba(0,0,0,.25)}
.brand{left:92px;top:22px;color:var(--paper);font-family:"Open Sans",sans-serif;font-weight:400;font-size:50px;letter-spacing:1px;line-height:1}
.brand-sub{left:160px;top:84px;color:var(--paper);font-size:14px;letter-spacing:1px}
.nav{top:58px;left:502px;display:flex;gap:0;color:var(--paper);font-size:16px}
.nav a{position:absolute;color:var(--paper);text-decoration:none;white-space:nowrap}
.nav a.current{border-bottom:1px solid var(--paper);padding-bottom:3px}
.login{left:1031px;top:53px;width:81px;height:31px;border:1.5px solid var(--paper);border-radius:16px;color:var(--paper);font-size:14px;text-align:center;line-height:28px}
.hero-title{left:0;width:1200px;top:228px;text-align:center;color:var(--paper);font-size:96px;line-height:1}
.hero-sub{left:0;width:1200px;top:344px;text-align:center;color:var(--paper);font-size:40px}
.slide-arrow{width:28px;height:28px;border-radius:50%;background:rgba(0,0,0,.6);top:314px}

/* Welcome */
.section-title{left:0;width:1200px;text-align:center;color:var(--plum);font-size:60px;line-height:1}
.lead{color:#555;font-size:15px;line-height:26px;text-align:center}
.feature-photo{width:176px;height:176px;border-radius:50%;border:4px solid #e6e6e6;top:844px}
.feature-name{width:300px;text-align:center;font-size:21px;top:1040px;color:var(--ink)}
.feature-text{width:280px;text-align:center;font-size:14px;line-height:20px;color:var(--grey);top:1078px}
.read-more{width:300px;text-align:center;font-size:14px;color:var(--plum);top:1148px}

/* Services */
.services{left:0;top:1233px;width:1200px;height:506px;background:var(--night);overflow:hidden}
.services-photo{position:absolute;left:600px;top:0;width:600px;height:506px;background:
  radial-gradient(ellipse 200px 250px at 260px 230px,#e9d9b4 0%,#bfa577 45%,transparent 80%),
  radial-gradient(ellipse 300px 300px at 400px 420px,#2a2a2e 0%,transparent 80%),
  linear-gradient(90deg,#0d0d0d 0%,#2a2522 40%,#3b3530 100%)}
.services-title{left:96px;top:66px;color:var(--paper);font-size:56px;line-height:1}
.service{width:260px;color:var(--paper)}
.service h3{font-weight:400;font-size:21px;letter-spacing:.3px;margin-bottom:6px}
.service p{font-size:12px;line-height:18px}
.service svg{position:absolute;left:-46px;top:0}

/* Testimonial */
.testimonial{left:0;top:1739px;width:1200px;height:395px;background:
  linear-gradient(135deg,#f4f4f4 0%,#ececec 40%,#f3f3f3 60%,#e9e9e9 100%)}
.avatar{left:554px;top:1952px;width:92px;height:92px;border-radius:50%;background:radial-gradient(circle at 50% 45%,#e9cfc0 0%,#d2ab98 60%,#c9a08d 100%);border:3px solid #fff}
.author{left:0;width:1200px;text-align:center;top:2060px;font-style:italic;font-size:18px;color:#333}

/* Blog */
.post-photo{top:2252px;width:311px;height:198px}
.post-title{width:311px;text-align:center;top:2462px;font-family:"Jost",sans-serif;font-size:17px;color:var(--ink)}
.post-date{width:311px;text-align:center;top:2488px;font-size:13px;color:#444}

/* Footer */
.footer{left:0;top:2555px;width:1200px;height:221px;background:var(--plum)}
.footer h4{position:absolute;top:36px;color:var(--paper);font-weight:400;font-size:16px;letter-spacing:.5px}
.footer p,.footer li{color:var(--paper);font-size:11.5px;line-height:18px}
.links{position:absolute;left:92px;top:72px;list-style:none}
.links li{line-height:24.5px;padding-left:12px;position:relative}
.links li::before{content:"";position:absolute;left:0;top:9px;border-left:5px solid var(--paper);border-top:3.5px solid transparent;border-bottom:3.5px solid transparent}
.email-field{position:absolute;left:909px;top:115px;width:148px;height:32px;background:var(--paper);color:#999;font-size:12px;line-height:32px;padding-left:12px}
.submit{position:absolute;left:1057px;top:115px;width:55px;height:32px;background:var(--coal);color:var(--paper);font-size:12px;text-align:center;line-height:32px}
.social{position:absolute;top:162px;width:32px;height:32px;border-radius:50%;border:1.5px solid var(--paper)}
.bottom-bar{left:0;top:2776px;width:1200px;height:99px;background:var(--coal)}
.copyright{left:0;width:1200px;text-align:center;top:2815px;color:var(--paper);font-size:12px}
</style>
</head>
<body>

<header class="hero abs">
  <div class="hero-photo" role="img" aria-label="Photo of a smiling stylist cutting a client's hair in the salon"></div>
  <div class="hero-shade"></div>
</header>
<div class="brand abs">Velora</div>
<div class="brand-sub abs">hair &amp; body</div>
<nav class="nav abs">
  <a class="current" style="left:0">HOME</a>
  <a style="left:88px">PRICING</a>
  <a style="left:190px">COMPANY</a>
  <a style="left:309px">CAREERS</a>
  <a style="left:414px">CONTACT US</a>
</nav>
<div class="login abs">LOG IN</div>
<h1 class="hero-title abs script">Velora Hair</h1>
<p class="hero-sub abs">Luxury Hair Salon</p>
<svg class="slide-arrow abs" style="left:72px" viewBox="0 0 28 28"><path d="M16 8l-6 6 6 6" fill="none" stroke="#fff" stroke-width="2"/></svg>
<svg class="slide-arrow abs" style="left:1105px" viewBox="0 0 28 28"><path d="M12 8l6 6-6 6" fill="none" stroke="#fff" stroke-width="2"/></svg>

<h2 class="section-title abs script" style="top:680px">Welcome to Velora Hair</h2>
<p class="lead abs" style="left:115px;width:970px;top:748px">Lorem Ipsum has been the industry's standard dummy text ever since the 1500s, when an unknown printer took a galley of type and scrambled it to make a type specimen book. It has survived not only five centuries, but also the leap into electronic typesetting, remaining essentially unchanged. It</p>

<div class="feature-photo abs" style="left:155px;background:radial-gradient(circle at 50% 40%,#c9b49c,#7b6a5c)" role="img" aria-label="Portrait of a woman with long blonde waves"></div>
<div class="feature-photo abs" style="left:502px;background:radial-gradient(circle at 50% 40%,#a76a78,#5a4a56)" role="img" aria-label="Portrait of a woman with long rose-toned hair"></div>
<div class="feature-photo abs" style="left:844px;background:radial-gradient(circle at 50% 40%,#8fa6b8,#2d3b4a)" role="img" aria-label="Portrait of a woman in a fur-trimmed winter hood"></div>

<h3 class="feature-name abs" style="left:93px;font-weight:400">TREATMENTS</h3>
<h3 class="feature-name abs" style="left:440px;font-weight:400">PRODUCTS</h3>
<h3 class="feature-name abs" style="left:782px;font-weight:400">ADVICE</h3>
<p class="feature-text abs" style="left:103px">It has survived not only five centuries, but also the leap into electronic typesetting, remaining essentially unchanged</p>
<p class="feature-text abs" style="left:450px">It has survived not only five centuries, but also the leap into electronic typesetting, remaining essentially unchanged</p>
<p class="feature-text abs" style="left:792px">It has survived not only five centuries, but also the leap into electronic typesetting, remaining essentially unchanged</p>
<a class="read-more abs" style="left:93px">Read More -&gt;</a>
<a class="read-more abs" style="left:440px">Read More -&gt;</a>
<a class="read-more abs" style="left:782px">Read More -&gt;</a>

<section class="services abs">
  <div class="services-photo" role="img" aria-label="Photo of a woman with voluminous platinum blonde curls"></div>
  <h2 class="services-title abs script">Our Services</h2>

  <div class="service abs" style="left:138px;top:160px">
    <svg width="36" height="36" viewBox="0 0 36 36" fill="none" stroke="#fff" stroke-width="2"><circle cx="8" cy="27" r="4"/><circle cx="16" cy="30" r="4"/><path d="M11 24L32 6M18 27L30 10"/></svg>
    <h3>HAIR CUTS</h3><p>Lorem Ipsum has been the industry's standard dummy text ever since</p>
  </div>
  <div class="service abs" style="left:435px;top:158px">
    <svg width="36" height="36" viewBox="0 0 36 36" fill="#fff"><rect x="4" y="6" width="26" height="13" rx="6"/><rect x="14" y="17" width="7" height="15" rx="2"/></svg>
    <h3>EXTENSIONS</h3><p>Lorem Ipsum has been the industry's standard dummy text ever since</p>
  </div>
  <div class="service abs" style="left:138px;top:258px">
    <svg width="36" height="36" viewBox="0 0 36 36" fill="#fff"><rect x="4" y="10" width="8" height="22" rx="2"/><rect x="14" y="6" width="8" height="26" rx="2"/><rect x="24" y="12" width="8" height="20" rx="2"/></svg>
    <h3>COLOURING</h3><p>Lorem Ipsum has been the industry's standard dummy text ever since</p>
  </div>
  <div class="service abs" style="left:435px;top:256px">
    <svg width="36" height="36" viewBox="0 0 36 36" fill="none" stroke="#fff" stroke-width="2"><path d="M8 30L28 6"/><path d="M11 26l-4-4M14 22l-4-4M17 18l-4-4M20 14l-4-4"/></svg>
    <h3>STRAIGHTENING</h3><p>Lorem Ipsum has been the industry's standard dummy text ever since</p>
  </div>
  <div class="service abs" style="left:138px;top:356px">
    <svg width="36" height="36" viewBox="0 0 36 36" fill="none" stroke="#fff" stroke-width="2.4"><circle cx="18" cy="18" r="14"/><path d="M12 8c6 4 6 10 0 14M18 6c6 6 6 14 0 22M24 10c4 4 4 10 0 14"/></svg>
    <h3>HIGHLIGHTING</h3><p>Lorem Ipsum has been the industry's standard dummy text ever since</p>
  </div>
  <div class="service abs" style="left:435px;top:354px">
    <svg width="36" height="36" viewBox="0 0 36 36" fill="#fff"><rect x="14" y="2" width="6" height="6"/><rect x="11" y="10" width="12" height="24" rx="2"/></svg>
    <h3>BRIDAL</h3><p>Lorem Ipsum has been the industry's standard dummy text ever since</p>
  </div>
</section>

<section class="testimonial abs"></section>
<h2 class="section-title abs script" style="top:1782px">Our Customers Say</h2>
<p class="lead abs" style="left:180px;width:840px;top:1871px;color:#666">We pride ourselves on being able to offer a private salon experience to our clients in the exclusive suburb of Ashgrove, where your hair design and colouring needs will be met with years of experience and current industry training and knowledge</p>
<svg class="abs" style="left:500px;top:1984px" width="24" height="28" viewBox="0 0 24 28"><path d="M16 4L6 14l10 10" fill="none" stroke="#777" stroke-width="2.5"/></svg>
<div class="avatar abs" role="img" aria-label="Small round portrait of a team member"></div>
<svg class="abs" style="left:678px;top:1984px" width="24" height="28" viewBox="0 0 24 28"><path d="M8 4l10 10L8 24" fill="none" stroke="#777" stroke-width="2.5"/></svg>
<p class="author abs">The Velora Team</p>

<h2 class="section-title abs script" style="top:2165px">Latest Blog</h2>
<div class="post-photo abs" style="left:94px;background:linear-gradient(120deg,#3a3c44 0%,#7a5c44 55%,#b8875a 100%)" role="img" aria-label="Photo of a woman in profile against a brick wall"></div>
<div class="post-photo abs" style="left:447px;background:linear-gradient(120deg,#e6ddc8 0%,#cdbb98 50%,#8d7d68 100%)" role="img" aria-label="Photo of a woman with long blonde hair in soft light"></div>
<div class="post-photo abs" style="left:797px;background:linear-gradient(120deg,#f2c060 0%,#a8652e 45%,#3e4a2c 100%)" role="img" aria-label="Photo of a woman's back-lit hair at sunset in a field"></div>
<h3 class="post-title abs" style="left:94px;font-weight:400">Neque porro quisquam est qui</h3>
<h3 class="post-title abs" style="left:447px;font-weight:400">Dolorem ipsum quia dolor sit amet</h3>
<h3 class="post-title abs" style="left:797px;font-weight:400">Quisquam est qui dolorem</h3>
<p class="post-date abs" style="left:94px">19/05/17</p>
<p class="post-date abs" style="left:447px">17/05/17</p>
<p class="post-date abs" style="left:797px">13/05/17</p>

<footer class="footer abs">
  <h4 style="left:92px">LINKS</h4>
  <ul class="links">
    <li>Customer Support</li><li>Documentation</li><li>Resources</li><li>General FAQs</li><li>Shortcodes</li>
  </ul>
  <h4 style="left:303px">VELORAHAIR</h4>
  <p class="abs" style="left:303px;top:72px;width:232px"> Lorem Ipsum has been the industry's standard dummy text ever since the 1500s, when an unknown printer took</p>
  <p class="abs" style="left:303px;top:132px;width:232px">a galley of type and scrambled it to make a type specimen book. It has survived not only five centuries, but also the leap into electronic type-</p>
  <h4 style="left:654px">GET IN TOUCH</h4>
  <p class="abs" style="left:654px;top:74px;width:200px;line-height:24px">Address : 214 Larkspur Lane,<br>Wembley Downs, WA</p>
  <p class="abs" style="left:654px;top:133px">Phone : 0400 555 019</p>
  <p class="abs" style="left:654px;top:170px">Email : hello@velorahair.example</p>
  <h4 style="left:909px">NEWSLETTER</h4>
  <p class="abs" style="left:909px;top:72px;width:200px">Your about us information would fit here nicely.</p>
  <div class="email-field">Email address</div>
  <div class="submit">Submit</div>
  <div class="social" style="left:909px"></div>
  <div class="social" style="left:957px"></div>
  <div class="social" style="left:1005px"></div>
</footer>
<div class="bottom-bar abs"></div>
<p class="copyright abs">Copyright © 2017. All Rights Reserved</p>

</body>
</html>
```